Marwick Law Letterhead

We need a new letterhead design for a Law Firm. The address for the law firm is 1475 Calloway Street, Suite 210, Houston, Texas 77041. Phone Number: 832-361-9027; Fax Number: 832-614-7359. The logo is uploaded to the project.

```html
<!DOCTYPE html>
<html lang="en">
<head>
<meta charset="utf-8">
<title>Marwick Law Letterhead</title>
<link href="https://fonts.googleapis.com/css2?family=Montserrat:wght@400;500;600&display=swap" rel="stylesheet">
<style>
  :root {
    --navy: #1b3160;
    --red: #d21f2d;
    --red-dark: #7c0b16;
    --ink: #1d1d22;
    --paper: #ffffff;
    --backdrop: #e8e9eb;
  }
  * { margin: 0; padding: 0; box-sizing: border-box; }
  html, body {
    width: 1200px; height: 960px; overflow: hidden;
    background: var(--backdrop);
    font-family: "Montserrat", Arial, sans-serif;
  }
  .letterhead {
    position: absolute; left: 280px; top: 27px;
    width: 640px; height: 905px;
    background: var(--paper);
    box-shadow: 0 6px 24px rgba(0,0,0,.12);
    overflow: hidden;
  }
  .letterhead__shapes { position: absolute; inset: 0; width: 640px; height: 905px; }
  .contact {
    position: absolute; left: 470px; top: 34px;
    color: #fff; font-size: 10px; line-height: 14px; font-weight: 400;
  }
  .contact__line { display: flex; align-items: center; gap: 6px; }
  .contact__icon { width: 10px; height: 10px; flex: none; }
  .contact__address { margin-bottom: 2px; }
  .brand {
    position: absolute; left: 48px; top: 66px;
    display: flex; align-items: center; gap: 10px;
  }
  .brand__mark { width: 22px; height: 22px; background: var(--navy); }
  .brand__name { color: var(--navy); font-size: 24px; font-weight: 500; letter-spacing: .5px; }
  .letter {
    position: absolute; left: 70px; top: 214px; width: 520px;
    color: var(--ink); font-size: 10.5px; line-height: 15px;
  }
  .recipient { margin-bottom: 16px; }
  .letter__para { margin-bottom: 16px; }
  .signoff { margin-top: 20px; font-size: 12px; font-weight: 500; }
  .signature {
    width: 96px; height: 30px; margin-top: 6px;
    background: linear-gradient(90deg, #f1f1f3, #e2e2e6);
    border-radius: 3px;
  }
</style>
</head>
<body>
<main class="letterhead">
  <svg class="letterhead__shapes" viewBox="0 0 640 905" aria-hidden="true">
    <defs>
      <linearGradient id="redSweep" x1="0" y1="0" x2="1" y2="0">
        <stop offset="0" stop-color="var(--red)"/>
        <stop offset=".65" stop-color="var(--red)"/>
        <stop offset="1" stop-color="var(--red-dark)"/>
      </linearGradient>
      <linearGradient id="redEdge" x1="0" y1="0" x2="1" y2="1">
        <stop offset="0" stop-color="var(--red)"/>
        <stop offset="1" stop-color="var(--red-dark)"/>
      </linearGradient>
    </defs>
    <polygon class="header-accent" points="308,0 640,0 640,131 448,149" fill="url(#redEdge)"/>
    <polygon class="header-band" points="322,0 640,0 640,131 452,141" fill="var(--navy)"/>
    <path class="footer-swoosh" d="M40 893 Q470 864 634 742 Q478 874 40 897 Z" fill="url(#redSweep)"/>
    <path class="footer-band" d="M0 905 Q482 892 640 772 L640 905 Z" fill="var(--navy)"/>
  </svg>

  <div class="contact">
    <p class="contact__address">1475 Calloway Street,<br>Suite 210, Houston,<br>Texas 77041</p>
    <p class="contact__line">
      <svg class="contact__icon" viewBox="0 0 10 10"><path d="M2 1 L4 1 L4.6 3 L3.4 3.8 Q4.4 5.8 6.2 6.6 L7 5.4 L9 6 L9 8 Q5 9 1 5 Q1 2.5 2 1 Z" fill="#fff"/></svg>
      832-361-9027
    </p>
    <p class="contact__line">
      <svg class="contact__icon" viewBox="0 0 10 10"><rect x="2.5" y="1" width="5" height="3" fill="#fff"/><rect x="1" y="4" width="8" height="4" rx="1" fill="#fff"/><rect x="2.5" y="6.5" width="5" height="2.5" fill="#fff"/></svg>
      832-614-7359
    </p>
  </div>

  <div class="brand">
    <span class="brand__mark"></span>
    <span class="brand__name">Marwick Law</span>
  </div>

  <section class="letter">
    <p class="recipient">Mr/s<br>First Name and Last Name<br>Company Name<br>Address</p>
    <p class="letter__para">Lorem ipsum dolor sit amet,consectetur adipiscing sed do eiusmod tempor incididunt laboreet dolore magna aliqua.Ut enim ad minim.veniam, quis nostrud exercitation ullamco laboris nisi ut aliquip exea commodo consequat.Lorem ipsum dolor sit amet,consectetur adipiscing sed do eiusmod tempor incididunt.labore et dolore magna aliqua. Ut enim</p>
    <p class="letter__para">Lorem ipsum dolor sit amet, consectetur adipiscing sed do eiusmod tempor incididunt labore et dolore magna aliqua. Ut enim ad minim veniam, quis nostrud exercitation ullamco laboris nisi ut aliquip exea commodo consequat.Duis aute irure dolor in reprehenderit in voluptate velit esse cillum irure dolor in reprehenderit in voluptate velit esse irure</p>
    <p class="letter__para">Lorem ipsum dolor sit amet, consectetur adipiscing sed do eiusmod tempor incididunt labore et dolore magna aliqua. consequat. Duis aute irure dolor in.reprehenderit in voluptate velit esse cillum dolore eu fugiat nulla pariatur. Excepteur sint occaecat cupidatat non proident, sunt in culpa qui officia deserunt mollit,</p>
    <p class="letter__para">Lorem ipsum dolor sit amet, consectetur adipiscing sed do eiusmod tempor incididunt labore et dolore magna aliqua. Ut enim Lorem ipsum dolor sit amet, consectetur adipiscing sed do eiusmod tempor incididunt labore et dolore magna aliqua. Ut enim Lorem ipsum aliqua.ipsum</p>
    <p class="letter__para">Lorem ipsum dolor sit amet, consectetur adipiscing sed do eiusmod tempor incididunt labore et dolore magna aliqua. Ut enim ad minim veniam, quis nostrud exercitation ullamco laboris nisi ut aliquip exea commodo consequat.Duis aute irure dolor in reprehenderit in voluptate velit esse cillum irure dolor in reprehenderit in voluptate velit esse irure</p>
    <p class="letter__para">Lorem ipsum dolor sit amet, consectetur adipiscing sed do eiusmod tempor incididunt labore et dolore magna aliqua. Ut enim ad minim veniam, quis nostrud exercitation ullamco laboris nisi ut aliquip exea commodo consequat.Duis aute irure dolor in reprehenderit in voluptate velit esse cillum irure dolor in reprehenderit in voluptate velit esse irure</p>
    <p class="signoff">Regards</p>
    <div class="signature" role="img" aria-label="Handwritten signature"></div>
  </section>
</main>
</body>
</html>
```